Personal training and nutrition business needs business card design

We need a business card that outlays our services and invites potential customers to join our team and take the first step to a healthier and more enjoyable life. We cater for any level of fitness and specialize in weight loss and conditioning, strength training, muscle gain and strength endurance. Whether you are just starting off or need some help getting to the next level of your journey we are here to get the job done.
We specialize in one on one or one on two personal training sessions and each program will be custom made to suit individual fitness goals of our clients

```html
<!DOCTYPE html>
<html lang="en">
<head>
<meta charset="utf-8">
<title>Stride &amp; Tempo — Business Card</title>
<link rel="stylesheet" href="https://fonts.googleapis.com/css2?family=Roboto:ital,wght@0,400;0,500;0,700;0,900;1,900&family=Roboto+Condensed:wght@500&display=swap">
<style>
  :root {
    --bg: #2a2a2a;
    --purple-deep: #553a8c;
    --purple-mid: #77479a;
    --purple-light: #9b56a0;
    --ink: #1c1c1c;
    --text: #2b2b2b;
    --paper: #f2f2f2;
    --white: #ffffff;
  }
  * { margin: 0; padding: 0; box-sizing: border-box; }
  html, body { width: 1200px; height: 1138px; overflow: hidden; }
  body {
    background: var(--bg);
    font-family: "Roboto", Arial, sans-serif;
    position: relative;
  }
  .card {
    position: absolute;
    border-radius: 14px;
    overflow: hidden;
  }
  /* Front */
  .card-front {
    left: 274px; top: 186px; width: 622px; height: 376px;
    background: linear-gradient(115deg, var(--purple-deep) 0%, var(--purple-mid) 50%, var(--purple-light) 100%);
    color: var(--white);
    text-align: center;
  }
  .front-wordmark {
    position: absolute; left: 0; right: 0; top: 140px;
    font-weight: 700; font-size: 52px; letter-spacing: 2px;
    line-height: 1;
  }
  .front-tagline {
    position: absolute; left: 0; right: 0; top: 208px;
    font-weight: 500; font-size: 15.5px; letter-spacing: 2.2px;
    color: #ece4f2;
  }
  /* Back */
  .card-back {
    left: 276px; top: 608px; width: 618px; height: 374px;
    background: var(--paper);
  }
  .back-waves { position: absolute; inset: 0; }
  .logo-block { position: absolute; left: 62px; top: 56px; width: 220px; }
  .logo-dot {
    width: 62px; height: 62px; border-radius: 50%;
    background: linear-gradient(135deg, var(--purple-deep), var(--purple-light));
    margin-left: 67px;
  }
  .logo-name {
    margin-top: 42px;
    font-weight: 700; font-size: 33px; line-height: 34px;
    color: var(--ink); letter-spacing: 1px;
  }
  .logo-tagline {
    margin-top: 6px;
    font-family: "Roboto Condensed", Arial, sans-serif;
    font-weight: 500; font-size: 9px; letter-spacing: 0.4px;
    color: var(--purple-mid);
  }
  .person { position: absolute; right: 34px; top: 46px; text-align: right; }
  .person-name {
    font-weight: 900; font-style: italic; font-size: 25px; letter-spacing: 1px;
    color: var(--purple-deep);
  }
  .person-role { font-size: 16px; color: var(--text); margin-top: 2px; }
  .address { margin-top: 34px; font-size: 16px; line-height: 25px; color: var(--text); }
  .edge-tab {
    position: absolute; right: -22px; top: 42px;
    width: 44px; height: 62px; border-radius: 50%;
    background: linear-gradient(180deg, var(--purple-mid), var(--purple-light));
  }
  .contacts {
    position: absolute; right: 30px; top: 278px;
    list-style: none; text-align: right;
  }
  .contacts li {
    display: flex; align-items: center; justify-content: flex-end;
    gap: 10px; height: 24px;
    font-size: 16px; color: var(--white);
  }
  .contacts svg { width: 14px; height: 14px; }
</style>
</head>
<body>

<section class="card card-front" aria-label="Card front">
  <div class="front-wordmark">STRIDE &amp; TEMPO</div>
  <div class="front-tagline">PERSONAL TRAINING &nbsp;|&nbsp; NUTRITION &nbsp;|&nbsp; MOTIVATION</div>
</section>

<section class="card card-back" aria-label="Card back">
  <svg class="back-waves" viewBox="0 0 618 374" preserveAspectRatio="none" aria-hidden="true">
    <defs>
      <linearGradient id="waveFill" x1="0" y1="1" x2="1" y2="0">
        <stop offset="0" stop-color="#553a8c"/>
        <stop offset="1" stop-color="#9b56a0"/>
      </linearGradient>
    </defs>
    <path d="M0,300 C120,338 250,330 360,284 C450,246 540,218 618,226 L618,374 L0,374 Z" fill="url(#waveFill)"/>
    <path d="M0,270 C140,326 260,306 380,252 C470,212 560,196 618,206" fill="none" stroke="#5b3d92" stroke-width="7"/>
    <path d="M0,314 C130,346 250,336 330,304" fill="none" stroke="#ffffff" stroke-width="6"/>
    <path d="M50,282 C150,320 240,310 300,292" fill="none" stroke="#b06aae" stroke-width="3" opacity="0.8"/>
  </svg>

  <div class="edge-tab" aria-hidden="true"></div>

  <div class="logo-block">
    <div class="logo-dot" aria-hidden="true"></div>
    <div class="logo-name">STRIDE<br>&amp; TEMPO</div>
    <div class="logo-tagline">PERSONAL TRAINING. NUTRITION. MOTIVATION</div>
  </div>

  <div class="person">
    <div class="person-name">MARCUS REED</div>
    <div class="person-role">Personal Trainer</div>
    <div class="address">1482 Cedar Ridge Lane<br>Oakview Texas 75321</div>
  </div>

  <ul class="contacts">
    <li>+1 (555) 214-7386
      <svg viewBox="0 0 16 16" aria-hidden="true"><path fill="#fff" d="M3 2h3l1 3-2 1.5a9 9 0 0 0 4.5 4.5L11 9l3 1v3a1 1 0 0 1-1 1A12 12 0 0 1 2 3a1 1 0 0 1 1-1z"/></svg>
    </li>
    <li>www.stridetempo.com
      <svg viewBox="0 0 16 16" aria-hidden="true"><g fill="none" stroke="#fff" stroke-width="1.3"><circle cx="8" cy="8" r="6.3"/><ellipse cx="8" cy="8" rx="2.8" ry="6.3"/><path d="M1.7 8h12.6M3 4.5h10M3 11.5h10"/></g></svg>
    </li>
    <li>marcus@stridetempo.com
      <svg viewBox="0 0 16 16" aria-hidden="true"><g fill="none" stroke="#fff" stroke-width="1.3"><rect x="1.5" y="3.5" width="13" height="9"/><path d="M1.5 3.5 8 9l6.5-5.5"/></g></svg>
    </li>
  </ul>
</section>

</body>
</html>
```